Need a cover for eBook:
Title is: 52 Blunders That Sink Your Indie-Released eBook.
Remarks about the title: I know that is difficult to design a cover with a number. You can add the word TOP (in caps or not) before 69 mistakes. It is not mandatory to insert the word TOP. It is up to you if you think you can create a better cover.
Subtitle is: A Starter's Handbook for Releasing Solo, Arranging Pictures and Words, Planning Pages, Raising Signups and Moving More Copies
Author: Walter P. Brenshaw
Publisher: Quillmark Works
The book made the presentation of errors that can occur during the production of an ebook. Title must be big, the title should be readable even when the image is reduced in size. No photo please.
I join my projects as an example. Do what you want but I need impact.

Target Market(s)

Book to sell first at Borvela Reader Shop. Target is authors, men or women, who want to produce ebooks.

Industry/Entity Type

Publishing Company

Font styles to use
Sans Serif

Colors
3176b5
9bcb3c

Requirements
Must have
• High readability when cover is small.
• Here is the definition of the word KILL
• put an end to or cause the failure or defeat of (something).
• "the committee voted to kill the project"
• synonyms: destroy, put an end to, end, extinguish, dash, quash, ruin, wreck, shatter, smash, crush, scotch, thwart; informalput the kibosh on, stymie, scuttle
• "this would kill all hopes of progress"
• veto, defeat, vote down, rule against, reject, throw out, overrule, overturn, put a stop to, quash, squash
• "an opposition attempt to kill the bill"
Nice to have
• I suggested 2 colors but you can you use another one or two. I want cover that sell. There is so bright ideas here. Come on down!
Should not have
• No picture or photo. If a photo or an object had power to the cover, you can insert one. I don't want a photo-collage.

```html
<!DOCTYPE html>
<html lang="en">
<head>
<meta charset="utf-8">
<title>52 Blunders That Sink Your Indie-Released eBook</title>
<link rel="stylesheet" href="https://fonts.googleapis.com/css2?family=Anton&family=Oswald:wght@700&family=EB+Garamond:wght@700&family=Russo+One&display=swap">
<style>
  :root {
    --cover-magenta: #ec008c;
    --title-blue: #12aee9;
    --title-blue-light: #5fd0f7;
    --title-blue-deep: #0a86c4;
    --title-edge: #0b3550;
    --ink: #111111;
    --paper: #ffffff;
    --burst-blue: #3a76b5;
    --burst-edge: #e0242a;
  }
  html, body {
    margin: 0;
    padding: 0;
    overflow: hidden;
    background: var(--cover-magenta);
  }
  .cover {
    position: relative;
    width: 927px;
    height: 1200px;
    overflow: hidden;
    background: var(--cover-magenta);
  }
  .cover-art {
    position: absolute;
    inset: 0;
    width: 927px;
    height: 1200px;
  }
  .title-number {
    font-family: "Russo One", sans-serif;
    font-size: 250px;
  }
  .title-word {
    font-family: "Anton", sans-serif;
    font-size: 160px;
    letter-spacing: 2px;
  }
  .title-bevel {
    fill: url(#titleFill);
    stroke: var(--title-edge);
    stroke-width: 5;
    paint-order: stroke;
    filter: url(#titleShadow);
  }
  .title-tail {
    font-family: "Oswald", sans-serif;
    font-weight: 700;
    font-size: 74px;
    fill: var(--ink);
    stroke: var(--paper);
    stroke-width: 4;
    paint-order: stroke;
    stroke-linejoin: round;
  }
  .subtitle {
    font-family: "EB Garamond", serif;
    font-weight: 700;
    font-size: 29px;
    fill: var(--ink);
  }
  .burst {
    fill: var(--burst-blue);
    stroke: var(--burst-edge);
    stroke-width: 2;
  }
  .burst-small {
    font-family: "EB Garamond", serif;
    font-weight: 700;
    font-size: 28px;
    fill: var(--ink);
  }
  .burst-accent {
    font-family: "EB Garamond", serif;
    font-weight: 700;
    font-size: 46px;
    fill: var(--cover-magenta);
  }
  .credit {
    font-family: "Oswald", sans-serif;
    font-weight: 700;
    font-size: 32px;
    fill: var(--ink);
  }
</style>
</head>
<body>
<main class="cover">
  <svg class="cover-art" viewBox="0 0 927 1200" xmlns="http://www.w3.org/2000/svg">
    <defs>
      <linearGradient id="titleFill" x1="0" y1="0" x2="0" y2="1">
        <stop offset="0" stop-color="var(--title-blue-light)"/>
        <stop offset="0.45" stop-color="var(--title-blue)"/>
        <stop offset="1" stop-color="var(--title-blue-deep)"/>
      </linearGradient>
      <filter id="titleShadow" x="-10%" y="-10%" width="120%" height="130%">
        <feDropShadow dx="3" dy="6" stdDeviation="5" flood-color="#3a0020" flood-opacity="0.55"/>
      </filter>
    </defs>

    <g class="title">
      <text class="title-number title-bevel" x="463" y="240" text-anchor="middle"
            textLength="560" lengthAdjust="spacingAndGlyphs">52</text>
      <text class="title-word title-bevel" x="463" y="386" text-anchor="middle"
            textLength="566" lengthAdjust="spacingAndGlyphs">Blunders</text>
      <text class="title-tail" x="464" y="492" text-anchor="middle"
            textLength="412" lengthAdjust="spacingAndGlyphs">That Sink Your</text>
      <text class="title-tail" x="479" y="557" text-anchor="middle"
            textLength="433" lengthAdjust="spacingAndGlyphs">Indie-Released</text>
      <text class="title-tail" x="478" y="624" text-anchor="middle"
            textLength="186" lengthAdjust="spacingAndGlyphs">eBook</text>
    </g>

    <g class="subtitle-block">
      <text class="subtitle" x="101" y="790">A Starter's Handbook for</text>
      <text class="subtitle" x="101" y="826">Releasing Solo,</text>
      <text class="subtitle" x="101" y="862">Arranging Pictures and Words,</text>
      <text class="subtitle" x="101" y="898">Planning Pages,</text>
      <text class="subtitle" x="101" y="934">Raising Signups</text>
    </g>

    <g class="burst-group">
      <polygon class="burst" points="755,726 712,839 830,808 736,885 853,917 733,937 818,1023 705,980 736,1098 659,1004 627,1121 607,1001 521,1086 564,973 446,1004 540,927 423,895 543,875 458,789 571,832 540,714 617,808 649,691 669,811"/>
      <text class="burst-small" x="660" y="872" text-anchor="middle">and</text>
      <text class="burst-accent" x="660" y="920" text-anchor="middle">Moving</text>
      <text class="burst-small" x="660" y="952" text-anchor="middle">More Copies</text>
    </g>

    <text class="credit credit-author" x="72" y="1118">Walter P. Brenshaw</text>
    <text class="credit credit-publisher" x="863" y="1122" text-anchor="end">Quillmark Works</text>
  </svg>
</main>
</body>
</html>
```